Harborline Claims Advocates Business card

We need to get business card Design for our Company we are Public Adjusters in Chicago Illinois - i like to see good combination and elements from my Company Logo. as well To be an two side design
Updates

Target Market(s)

Home /Business owner Property Managers

Industry/Entity Type

Business

Contact Information for Business Card

to show the Element of our logo i will Like 3D

Font styles to use
Sans Serif

Requirements
Must have
• Logo and Element of the Logo in 3D
Nice to have
• Logo That we Provide 3D Same Colors or open for suggestions
Should not have
• unleare view -

```html
<!DOCTYPE html>
<html lang="en">
<head>
<meta charset="UTF-8">
<title>Harborline Claims Advocates — Business Card</title>
<link href="https://fonts.googleapis.com/css2?family=Open+Sans:wght@400;600;700&display=swap" rel="stylesheet">
<style>
  :root {
    --backdrop: #e9e9ec;
    --card-white: #f7f7f9;
    --brand-blue: #25259a;
    --brand-blue-deep: #1b1b86;
    --brand-blue-light: #3a3ab4;
    --accent-orange: #d9573c;
    --text-light: #ffffff;
    --name-blue: #1f2594;
  }
  html, body {
    margin: 0;
    padding: 0;
    width: 1200px;
    height: 900px;
    overflow: hidden;
    background: var(--backdrop);
    font-family: "Open Sans", Arial, sans-serif;
  }
  .canvas {
    position: relative;
    width: 1200px;
    height: 900px;
  }
  .business-card {
    position: absolute;
    left: 150px;
    top: 172px;
    width: 900px;
    height: 556px;
    border-radius: 22px;
    overflow: hidden;
    background: var(--card-white);
    box-shadow: 0 10px 30px rgba(0,0,0,0.12);
  }
  .card-panel {
    position: absolute;
    inset: 0;
    width: 900px;
    height: 556px;
  }
  .holder-name {
    position: absolute;
    left: 46px;
    top: 62px;
    margin: 0;
    font-size: 30px;
    line-height: 41px;
    font-weight: 700;
    color: var(--text-light);
    letter-spacing: 0.2px;
  }
  .holder-title {
    position: absolute;
    left: 46px;
    top: 102px;
    margin: 0;
    font-size: 23px;
    line-height: 31px;
    font-weight: 400;
    color: var(--text-light);
  }
  .contact-list {
    position: absolute;
    left: 46px;
    top: 284px;
    margin: 0;
    padding: 0;
    list-style: none;
    color: var(--text-light);
    font-size: 23px;
  }
  .contact-list li {
    display: flex;
    align-items: center;
    height: 41px;
    white-space: nowrap;
  }
  .contact-icon {
    width: 22px;
    height: 22px;
    margin-right: 11px;
    flex: none;
  }
  .postal-address {
    position: absolute;
    left: 46px;
    top: 436px;
    margin: 0;
    font-style: normal;
    font-size: 23px;
    line-height: 33px;
    color: var(--text-light);
  }
  .brand-mark {
    position: absolute;
    left: 590px;
    top: 220px;
    width: 130px;
    height: 130px;
    border-radius: 50%;
    background: var(--brand-blue);
  }
  .brand-name {
    position: absolute;
    left: 455px;
    width: 400px;
    top: 466px;
    margin: 0;
    text-align: center;
    font-size: 25px;
    line-height: 34px;
    font-weight: 700;
    color: var(--name-blue);
    white-space: nowrap;
  }
</style>
</head>
<body>
<main class="canvas">
  <section class="business-card" aria-label="Business card front">
    <svg class="card-panel" viewBox="0 0 900 556" aria-hidden="true">
      <defs>
        <linearGradient id="panelBlue" x1="0" y1="0" x2="1" y2="1">
          <stop offset="0" stop-color="var(--brand-blue-deep)"/>
          <stop offset="0.45" stop-color="var(--brand-blue-light)"/>
          <stop offset="1" stop-color="var(--brand-blue-deep)"/>
        </linearGradient>
      </defs>
      <path class="panel-edge" fill="var(--accent-orange)"
            d="M0,0 H338 C440,40 512,100 510,160 L504,360 C500,440 412,520 358,556 H0 Z"/>
      <path class="panel-fill" fill="url(#panelBlue)"
            d="M0,0 H325 C420,40 500,100 498,160 L492,360 C488,440 400,520 346,556 H0 Z"/>
    </svg>

    <h1 class="holder-name">Daniel Hartley</h1>
    <p class="holder-title">Managing Director</p>

    <ul class="contact-list">
      <li>
        <svg class="contact-icon" viewBox="0 0 24 24" aria-hidden="true">
          <path fill="#fff" d="M3 9c0-3 4-5 9-5s9 2 9 5v1.5h-4.5V8.5h-9v2H3z"/>
          <path fill="#fff" d="M6 12h12l2 8H4z"/>
          <circle cx="12" cy="16" r="2.2" fill="var(--brand-blue)"/>
        </svg>
        <span>044-987 654 321</span>
      </li>
      <li>
        <svg class="contact-icon" viewBox="0 0 24 24" aria-hidden="true">
          <rect x="2" y="5" width="20" height="14" fill="#fff"/>
          <path d="M2.5 5.5 12 13l9.5-7.5" fill="none" stroke="var(--brand-blue)" stroke-width="1.8"/>
        </svg>
        <span>hello@harborlineclaims.com</span>
      </li>
      <li>
        <svg class="contact-icon" viewBox="0 0 24 24" aria-hidden="true">
          <g fill="none" stroke="#fff" stroke-width="2.2" stroke-linecap="round">
            <path d="M10 14l4-4"/>
            <path d="M11 7l2-2a3.5 3.5 0 0 1 5 5l-2 2"/>
            <path d="M13 17l-2 2a3.5 3.5 0 0 1-5-5l2-2"/>
          </g>
        </svg>
        <span>www.harborlineclaims.com</span>
      </li>
    </ul>

    <address class="postal-address">12345, adrress goes here,<br>country name,12345</address>

    <div class="brand-mark" aria-hidden="true"></div>
    <p class="brand-name">Harborline Claims Advocates</p>
  </section>
</main>
</body>
</html>
```